Classy, Elegant, Simple Business Card Design

Looking to have a classy, simple, and elegant design. Want a top notch designed business card. I really like the look of the new torvane credit card. I also like the design I attached. I am trying to reach 21-29 year old females for booking us for there wedding or event. We offer Disc Jockey Service, Photo Booth Rentals, and Uplighting .

Target Market(s)

21-28 year old females

Contact Information for Business Card

Has to have logo, website, email, and phone number

Font styles to use
Other font styles liked:
• open to font choice, modern, clean
Designer to choose
33a6d7
0791cd
0555a3
ffffff

Requirements
Must have
• Has to have logo, website, email, and phone number
Nice to have
• I really like the design of the new torvane credit card. I also included my logo and some designs I like
Should not have
• clutter or too much info

```html
<!DOCTYPE html>
<html lang="en">
<head>
<meta charset="utf-8">
<title>Tidewell Event Group – Business Card</title>
<link href="https://fonts.googleapis.com/css2?family=Poppins:wght@300;400;500;600&display=swap" rel="stylesheet">
<style>
  :root {
    --sky: #33a6d7;
    --azure: #0791cd;
    --navy: #0555a3;
    --white: #ffffff;
    --ink: #3a3f47;
    --muted: #8a9098;
    --stage: #2b2c2e;
  }
  * { margin: 0; padding: 0; box-sizing: border-box; }
  html, body { width: 1200px; height: 885px; overflow: hidden; }
  body {
    background: var(--stage);
    font-family: "Poppins", sans-serif;
    position: relative;
  }
  .card {
    position: absolute;
    width: 560px;
    height: 320px;
    background: var(--white);
    overflow: hidden;
  }
  .card--front { left: 70px; top: 90px; }
  .card--back { left: 570px; top: 475px; }

  /* Front */
  .front-wordmark {
    position: absolute;
    left: 0; right: 0; top: 95px;
    text-align: center;
  }
  .wordmark {
    font-weight: 500;
    color: var(--navy);
    letter-spacing: 0.04em;
  }
  .front-wordmark .wordmark { font-size: 34px; display: inline-flex; align-items: center; gap: 14px; }
  .wordmark-dot {
    width: 16px; height: 16px; border-radius: 50%;
    background: var(--azure); display: inline-block;
  }
  .services {
    position: absolute;
    left: 0; right: 0; bottom: 48px;
    text-align: center;
    font-size: 13px;
    color: var(--ink);
    letter-spacing: 0.02em;
  }
  .services .sep { color: var(--azure); margin: 0 5px; }

  /* Back */
  .band {
    position: absolute;
    background: linear-gradient(180deg, var(--sky), var(--navy));
  }
  .band--left { left: 0; top: 150px; width: 12px; height: 150px; }
  .band--right { right: 0; top: 18px; width: 12px; height: 118px; }
  .back-mark {
    position: absolute;
    right: 48px; top: 60px;
    width: 200px;
    text-align: center;
  }
  .back-mark .wordmark { font-size: 38px; display: block; line-height: 1.1; }
  .identity { position: absolute; left: 40px; top: 120px; }
  .identity .wordmark { font-size: 22px; display: block; }
  .person-name {
    margin-top: 12px;
    font-size: 21px;
    font-weight: 500;
    color: var(--azure);
  }
  .person-title {
    font-size: 14px;
    font-weight: 300;
    color: var(--muted);
    margin-top: -2px;
  }
  .contacts {
    list-style: none;
    margin-top: 14px;
    font-size: 14px;
    color: var(--ink);
  }
  .contacts li { display: flex; align-items: center; gap: 10px; line-height: 22px; }
  .contacts svg { width: 13px; height: 13px; fill: var(--azure); flex: none; }
</style>
</head>
<body>

  <section class="card card--front" aria-label="Business card front">
    <div class="front-wordmark">
      <span class="wordmark"><span class="wordmark-dot"></span>Tidewell Event Group</span>
    </div>
    <p class="services">Disc Jockey Service<span class="sep">•</span>Photo Booth Rentals<span class="sep">•</span>Uplighting .</p>
  </section>

  <section class="card card--back" aria-label="Business card back">
    <span class="band band--left"></span>
    <span class="band band--right"></span>

    <div class="back-mark">
      <span class="wordmark">Tidewell</span>
    </div>

    <div class="identity">
      <span class="wordmark">Tidewell Event Group</span>
      <p class="person-name">Daniel Hart</p>
      <p class="person-title">President</p>
      <ul class="contacts">
        <li>
          <svg viewBox="0 0 24 24" aria-hidden="true"><path d="M6.6 10.8a15.1 15.1 0 0 0 6.6 6.6l2.2-2.2a1 1 0 0 1 1-.25 11.4 11.4 0 0 0 3.6.57 1 1 0 0 1 1 1V20a1 1 0 0 1-1 1A17 17 0 0 1 3 4a1 1 0 0 1 1-1h3.5a1 1 0 0 1 1 1c0 1.25.2 2.45.57 3.57a1 1 0 0 1-.25 1z"/></svg>
          555-014-2290
        </li>
        <li>
          <svg viewBox="0 0 24 24" aria-hidden="true"><path d="M2 5h20v14H2z M2 5l10 8 10-8" fill="none" stroke="#0791cd" stroke-width="2"/></svg>
          info@tidewellevents.com
        </li>
        <li>
          <svg viewBox="0 0 24 24" aria-hidden="true"><circle cx="12" cy="12" r="10"/></svg>
          www.tidewellevents.com
        </li>
      </ul>
    </div>
  </section>

</body>
</html>
```